Simple one page Wordpress website

We need a quick turnaround single page wordpress website.
The design needs to be very simple and clean.
We already have some design assets (logos and colours etc) and some draft copy for the page.

We need all the files for us to be able to create a wordpress site. We can do this ourselves and we will host it.

```html
<!DOCTYPE html>
<html lang="en">
<head>
<meta charset="utf-8">
<title>VetNova</title>
<link href="https://fonts.googleapis.com/css2?family=Montserrat:wght@500;600;700&family=Lato:wght@400;700&display=swap" rel="stylesheet">
<style>
:root{
  --green:#8cb71f;
  --green-dark:#7aa416;
  --navy:#2d2c4b;
  --text:#4a4a4a;
  --muted:#efefef;
  --light:#f6f6f6;
  --black:#0c0c0c;
  --white:#ffffff;
}
*{box-sizing:border-box;margin:0;padding:0}
html,body{width:1200px;height:3970px;overflow:hidden}
body{font-family:"Lato",sans-serif;color:var(--text);background:var(--white);position:relative}
h1,h2,h3,h4,.nav a,.btn{font-family:"Montserrat",sans-serif}
.rule{display:block;width:34px;height:5px;background:var(--green);margin:0 auto}

/* header */
.site-header{height:82px;border-top:5px solid var(--green);display:flex;align-items:center;padding-left:132px;background:var(--white)}
.brand{display:flex;align-items:center;gap:8px;font-family:"Montserrat",sans-serif;font-weight:600;font-size:38px;color:#4d8fc0;letter-spacing:1px}
.brand-dot{width:14px;height:14px;background:var(--green)}
.nav{display:flex;gap:34px;margin-left:80px}
.nav a{font-size:13.5px;font-weight:500;color:#222;text-decoration:none}
.nav a.active{color:var(--green)}

/* hero */
.hero{position:relative;height:640px;background:linear-gradient(180deg,#f1ede8 0%,#e9e4de 55%,#d9d2cb 100%);text-align:center}
.hero-photo{position:absolute;inset:0;background:radial-gradient(ellipse 38% 32% at 54% 68%,#8a5a36 0%,#b07b4a 45%,rgba(220,205,190,0) 100%)}
.hero-content{position:relative;padding-top:88px}
.hero h1{font-size:55px;font-weight:700;color:#222;letter-spacing:1px}
.hero p{font-size:13px;line-height:27px;color:#333;width:870px;margin:14px auto 0}
.btn{display:inline-block;margin-top:14px;background:var(--green);color:var(--white);font-weight:600;font-size:15px;padding:11px 20px;border-radius:22px}
.arrow{position:absolute;top:262px;width:42px;height:42px;border-radius:50%;background:var(--white);display:flex;align-items:center;justify-content:center}
.arrow.prev{left:59px}.arrow.next{right:59px}

/* mission */
.mission{height:355px;background:var(--muted);text-align:center;padding-top:82px}
.section-title{font-size:35px;font-weight:700;color:var(--navy);letter-spacing:.5px}
.mission .rule{margin-top:12px}
.mission p{font-size:23px;line-height:37px;color:#333;width:800px;margin:26px auto 0}

/* capabilities */
.capabilities{height:574px;position:relative}
.cap-photo{position:absolute;left:134px;top:105px;width:463px;height:391px;border:3px solid var(--green);padding:6px;background:var(--white)}
.cap-photo div{width:100%;height:100%;background:linear-gradient(135deg,#b7c9c4 0%,#dfe3df 45%,#f1efea 70%,#9ab8b0 100%)}
.cap-text{position:absolute;left:647px;top:176px;width:442px}
.cap-text h2{font-size:35px;font-weight:700;color:var(--navy)}
.cap-text .rule{margin:14px 0 0}
.cap-list{list-style:none;margin-top:28px}
.cap-list li{position:relative;padding-left:25px;font-size:13.5px;line-height:26.5px;color:#444}
.cap-list li svg{position:absolute;left:0;top:7px}

/* deployment */
.deployment{height:627px;background:linear-gradient(180deg,#90ba22 0%,#8ab51e 100%);text-align:center;color:var(--white);padding-top:80px}
.deployment h2{font-size:35px;line-height:49px;font-weight:700;color:var(--white)}
.deployment .rule{background:var(--white);margin-top:12px}
.deployment .intro{font-size:13.5px;line-height:25px;width:830px;margin:20px auto 0}
.features{display:flex;justify-content:center;gap:79px;margin-top:40px}
.feature{width:120px}
.feature .icon{width:120px;height:120px;border-radius:50%;background:var(--white);display:flex;align-items:center;justify-content:center}
.feature h3{font-size:16px;line-height:25px;font-weight:600;margin-top:10px;white-space:nowrap;margin-left:-30px;margin-right:-30px}
.deployment .contact{font-family:"Montserrat",sans-serif;font-size:14px;margin-top:48px}
.deployment .contact u{color:var(--white)}

/* joint venture */
.venture{height:714px;position:relative;text-align:center;padding-top:82px}
.venture .rule{margin-top:12px}
.venture-text{position:absolute;left:132px;top:188px;width:468px;text-align:justify}
.venture-text p{font-size:13px;line-height:26.5px;color:#444;margin-bottom:26px}
.venture-text .hl{color:var(--green)}
.vphoto{position:absolute}
.vphoto.top{left:698px;top:184px;width:370px;height:345px;background:linear-gradient(135deg,#3a3531 0%,#7d6a5c 40%,#c9c1ba 70%,#efece8 100%)}
.vphoto.low{left:657px;top:374px;width:240px;height:224px;border:3px solid var(--white);background:linear-gradient(180deg,#c7c2bd 0%,#b1aaa2 50%,#c48b4f 80%,#a9a29a 100%)}

/* team */
.team{height:614px;background:var(--light);text-align:center;padding-top:82px}
.team .rule{margin-top:12px}
.members{display:flex;justify-content:center;gap:13px;margin-top:40px}
.member{width:225px}
.member .photo{height:244px;border-radius:22px 22px 0 0}
.member h4{font-size:16px;font-weight:600;color:#222;margin-top:24px;letter-spacing:.5px}
.member p{font-size:12.5px;line-height:24px;color:#555;margin-top:6px;padding:0 12px}

/* footer */
.site-footer{height:364px;background:var(--black);color:var(--white);position:relative}
.footer-brand{position:absolute;left:124px;top:124px;font-family:"Montserrat",sans-serif;font-weight:600;font-size:60px;letter-spacing:2px;color:var(--white)}
.fcol{position:absolute;top:68px}
.fcol h4{font-size:17px;font-weight:700;letter-spacing:.5px}
.fcol ul{list-style:none;margin-top:14px}
.fcol li{font-size:13.5px;line-height:28px}
.fcol.quick{left:427px}.fcol.other{left:627px}.fcol.contact{left:827px}
.fcol.contact li{display:flex;align-items:center;gap:12px;line-height:36px}
.socials{display:flex;gap:14px;margin-top:18px}
.socials span{width:29px;height:29px;border-radius:50%;background:var(--green)}
.footer-rule{position:absolute;left:93px;right:107px;top:292px;height:1px;background:#555}
.copyright{position:absolute;left:0;right:0;top:317px;text-align:center;font-size:11px;font-weight:700}
</style>
</head>
<body>

<header class="site-header">
  <div class="brand"><span>VetNova</span><span class="brand-dot"></span></div>
  <nav class="nav">
    <a class="active" href="#home">HOME</a>
    <a href="#mission">MISSION</a>
    <a href="#capabilities">CAPABILITIES</a>
    <a href="#deployment">VETERINARY DEPLOYMENT</a>
    <a href="#venture">JOINT VENTURE</a>
    <a href="#team">TEAM</a>
  </nav>
</header>

<section class="hero" id="home">
  <div class="hero-photo" role="img" aria-label="A dog and a cat lying together on a floor in a bright living room"></div>
  <div class="hero-content">
    <h1>WELCOME TO VETNOVA</h1>
    <p>Lorem ipsum dolor sit amet, consectetur adipiscing elit, sed do eiusmod tempor incididunt ut labore et dolore magna aliqua. Quis ipsum suspendisse ultrices gravida. Risus commodo viverra maecenas accumsan lacus vel facilisis.</p>
    <span class="btn">GET STARTED</span>
  </div>
  <span class="arrow prev"><svg width="10" height="10" viewBox="0 0 10 10"><path d="M6.5 1.5 3 5l3.5 3.5" fill="none" stroke="#8cb71f" stroke-width="1.5"/></svg></span>
  <span class="arrow next"><svg width="10" height="10" viewBox="0 0 10 10"><path d="M3.5 1.5 7 5 3.5 8.5" fill="none" stroke="#8cb71f" stroke-width="1.5"/></svg></span>
</section>

<section class="mission" id="mission">
  <h2 class="section-title">MISSION</h2>
  <span class="rule"></span>
  <p>VetNova is deploying a Software as a Service (SaaS) platform to facilitate the efficient collection, transmission, secure storage and anonymised analysis of data integral to animal diagnostics.</p>
</section>

<section class="capabilities" id="capabilities">
  <div class="cap-photo"><div role="img" aria-label="Two vets in scrubs and blue gloves bandaging a small white terrier's paw"></div></div>
  <div class="cap-text">
    <h2>CAPABILITIES</h2>
    <span class="rule"></span>
    <ul class="cap-list">
      <li><svg width="13" height="13" viewBox="0 0 13 13"><circle cx="6.5" cy="6.5" r="6.5" fill="#8cb71f"/><path d="M5 3.5 8 6.5 5 9.5" fill="none" stroke="#fff" stroke-width="1.6"/></svg>Originally developed for the human market, the core platform has been deployed inthe UK and Ireland and has been used to securely process nearly 3 million cases</li>
      <li><svg width="13" height="13" viewBox="0 0 13 13"><circle cx="6.5" cy="6.5" r="6.5" fill="#8cb71f"/><path d="M5 3.5 8 6.5 5 9.5" fill="none" stroke="#fff" stroke-width="1.6"/></svg>The platform has been widely used by leading pharmacies, employers, the public health service and most of the UK's largest private sector laboratories</li>
    </ul>
  </div>
</section>

<section class="deployment" id="deployment">
  <h2>TURNKEY INITIAL VETERINARY DEPLOYMENT –<br>ANIMAL HEALTH AND WELFARE PATHWAY</h2>
  <span class="rule"></span>
  <p class="intro">VetNova is finalising the design of a bespoke platform to facilitate the collection and processing of data and tests for the Animal Health and Welfare Pathway. Key elements include:</p>
  <div class="features">
    <div class="feature">
      <div class="icon"><svg width="72" height="72" viewBox="0 0 72 72" fill="none" stroke="#8cb71f" stroke-width="2.5"><circle cx="42" cy="30" r="18"/><path d="M29 43 12 60"/><path d="M35 38V30M42 38V22M49 38V26"/></svg></div>
      <h3>Facilitated data<br>collection at the<br>farm by vets.</h3>
    </div>
    <div class="feature">
      <div class="icon"><svg width="72" height="72" viewBox="0 0 72 72" fill="none" stroke="#8cb71f" stroke-width="2.5"><path d="M36 8 60 16v18c0 16-11 26-24 30C23 60 12 50 12 34V16Z"/><path d="m25 36 8 8 15-16"/></svg></div>
      <h3>Secure and efficient<br>processing of test<br>samples by labs</h3>
    </div>
    <div class="feature">
      <div class="icon"><svg width="72" height="72" viewBox="0 0 72 72" fill="none" stroke="#8cb71f" stroke-width="2.5"><rect x="10" y="20" width="52" height="34"/><path d="M20 48V38M28 48V32M36 48V36M44 48V28M52 48V34"/><path d="M28 60h16"/></svg></div>
      <h3>Digital results<br>reporting</h3>
    </div>
    <div class="feature">
      <div class="icon"><svg width="72" height="72" viewBox="0 0 72 72" fill="none" stroke="#8cb71f" stroke-width="2.5"><path d="M16 8h28l10 10v40H16Z"/><path d="M24 22h14M24 30h10M24 38h8"/><circle cx="46" cy="44" r="9"/><path d="m42 44 3 3 5-5M53 51l7 7"/></svg></div>
      <h3>Invoice<br>support</h3>
    </div>
    <div class="feature">
      <div class="icon"><svg width="72" height="72" viewBox="0 0 72 72" fill="none" stroke="#8cb71f" stroke-width="2.5"><rect x="10" y="14" width="44" height="34"/><circle cx="42" cy="42" r="12"/><path d="M37 46v-6M42 46v-9M47 46v-4M51 51l9 9"/></svg></div>
      <h3>Data analysis<br>reporting</h3>
    </div>
  </div>
  <p class="contact">Interested parties seeking further information should contact us at <u>info@vetnova.example</u></p>
</section>

<section class="venture" id="venture">
  <h2 class="section-title">VETNOVA IS A JOINT VENTURE BETWEEN</h2>
  <span class="rule"></span>
  <div class="venture-text">
    <p><span class="hl">Fieldstone Solutions Limited (FSL)</span>, an innovative veterinary-led, close to market sustainable food research organisation. FSL brings together a team of highly experienced vets representing key opinion leaders within the livestock industry and additional technical support staff through its shareholder practice Ashgrove Veterinary Group, Yorkshire. Ashgrove is a 75 year old six centre veterinary group in North Yorkshire, focusing on livestock and equine. In turn Ashgrove is part of VetAlliance, an independent grouping of 40+ Farm and Equine practices across the UK.</p>
    <p><span class="hl">Clearpath Diagnostics Limited (CDX), is a rapidly growing Software as a Service platform provider in the digital health market. CDX deploys its agile and collaborative software development process working in,</span> partnership with its clients, using the skills of both parties to build the best solutions as effectively and efficiently as possible. Its clients include some of the country's largest pharmacies, employers and laboratories across the UK.</p>
  </div>
  <div class="vphoto top" role="img" aria-label="A vet examining a tabby and white cat's ear with an otoscope"></div>
  <div class="vphoto low" role="img" aria-label="A golden dog lying on a clinic floor beside a monitor"></div>
</section>

<section class="team" id="team">
  <h2 class="section-title">MEET OUR TEAM</h2>
  <span class="rule"></span>
  <div class="members">
    <div class="member"><div class="photo" role="img" aria-label="Portrait of a smiling team member in a white top" style="background:linear-gradient(180deg,#ececec,#dcdcdc)"></div><h4>JENIFFER</h4><p>Lorem ipsum dolor sit amet, conse ctetur adipiscing elit, sed do eiusm od tempor incididunt.</p></div>
    <div class="member"><div class="photo" role="img" aria-label="Portrait of a smiling team member in a blue check shirt" style="background:linear-gradient(180deg,#d3d6d8,#6f9cc7)"></div><h4>JOHN SMITH</h4><p>Lorem ipsum dolor sit amet, conse ctetur adipiscing elit, sed do eiusm od tempor incididunt.</p></div>
    <div class="member"><div class="photo" role="img" aria-label="Portrait of a smiling team member pointing aside" style="background:linear-gradient(180deg,#c9d6e8,#e3e8ef)"></div><h4>JENIFFER</h4><p>Lorem ipsum dolor sit amet, conse ctetur adipiscing elit, sed do eiusm od tempor incididunt.</p></div>
    <div class="member"><div class="photo" role="img" aria-label="Portrait of a smiling team member in a beige jacket" style="background:linear-gradient(180deg,#9c9c9c,#bca98c)"></div><h4>JOHN SMITH</h4><p>Lorem ipsum dolor sit amet, conse ctetur adipiscing elit, sed do eiusm od tempor incididunt.</p></div>
  </div>
</section>

<footer class="site-footer">
  <div class="footer-brand">VetNova</div>
  <div class="fcol quick"><h4>QUICK LINKS</h4><ul><li>Home</li><li>Mission</li><li>Capabilities</li><li>Veterinary Deployment</li><li>Joint Venture</li><li>Team</li></ul></div>
  <div class="fcol other"><h4>OTHER LINKS</h4><ul><li>FAQ's</li><li>About Us</li><li>Blog</li><li>Privacy Policy</li><li>Terms &amp; Conditions</li></ul></div>
  <div class="fcol contact"><h4>CONTACT US</h4>
    <ul>
      <li><svg width="10" height="14" viewBox="0 0 10 14"><path d="M5 0a5 5 0 0 0-5 5c0 4 5 9 5 9s5-5 5-9a5 5 0 0 0-5-5Zm0 7a2 2 0 1 1 0-4 2 2 0 0 1 0 4Z" fill="#fff"/></svg>123 Lorem ipsum dolor sit amet</li>
      <li><svg width="12" height="12" viewBox="0 0 12 12"><path d="M2.5 0 4.5 3 3 4.5a7 7 0 0 0 4.5 4.5L9 7.5l3 2-1.5 2.5C5 12 0 7 0 1.5Z" fill="#fff"/></svg>+1 888 888 8888</li>
      <li><svg width="13" height="10" viewBox="0 0 13 10"><rect width="13" height="10" fill="#fff"/><path d="m0 0 6.5 5L13 0" fill="none" stroke="#0c0c0c" stroke-width="1.2"/></svg>hello@vetnova.example</li>
    </ul>
    <div class="socials"><span></span><span></span><span></span><span></span></div>
  </div>
  <div class="footer-rule"></div>
  <p class="copyright">© Copyrights 2022 VetNova | &nbsp;&nbsp; All rights reserved.</p>
</footer>

</body>
</html>
```